Newsletter Ad

I am looking for someone to design an advertisement for a mother's club newsletter. 4" wide X by 5" tall (and 2.5" wide X 5" tall if possible).

I'm a psychotherapist, so want the ad to look professional, but modern. I have a logo with my photo attached that can be incorporated into the design. The colors of my website are turquoise and white. I'd like to keep with that theme...so maybe some turquoise blocking to match the logo font color.

I'm uploading a logo as well as an ad draft with the content I'd like listed in the ad.

```html
<!DOCTYPE html>
<html lang="en">
<head>
<meta charset="utf-8">
<title>Dana Rowell, MA, MFT – Psychotherapy Ad</title>
<link rel="stylesheet" href="https://fonts.googleapis.com/css2?family=Questrial&display=swap">
<style>
  :root {
    --teal: #3d8f8c;
    --teal-light: #4a9c98;
    --teal-dark: #327f7c;
    --ink: #1b1b1b;
    --black: #0b0b0b;
    --white: #ffffff;
    --photo-warm: #8a6a4c;
    --photo-dark: #2a221c;
  }
  * { box-sizing: border-box; margin: 0; padding: 0; }
  html, body { width: 961px; height: 1200px; overflow: hidden; background: var(--white); }
  body { font-family: "Questrial", "Century Gothic", sans-serif; }

  .ad { position: relative; width: 961px; height: 1200px; background: var(--white); overflow: hidden; }

  .side-column { position: absolute; left: 0; top: 0; width: 371px; height: 913px; background: var(--black); }
  .portrait {
    position: absolute; left: 0; top: 0; width: 371px; height: 640px;
    background: radial-gradient(ellipse at 45% 40%, var(--photo-warm) 0%, #5a4431 45%, var(--photo-dark) 100%);
  }

  .service-panel {
    position: absolute; left: 371px; top: 0; width: 590px; height: 913px;
    background: linear-gradient(160deg, var(--teal-light) 0%, var(--teal) 50%, var(--teal-dark) 100%);
  }

  .name-band {
    position: absolute; left: 371px; top: 62px; width: 590px; height: 110px;
    background: var(--white);
    box-shadow: 0 4px 6px rgba(0, 0, 0, 0.25);
    display: flex; align-items: center; justify-content: center;
    color: var(--teal); font-size: 47px; letter-spacing: 0; white-space: nowrap;
  }

  .centered { position: absolute; transform: translate(-50%, -50%); white-space: nowrap; text-align: center; }

  .headline { left: 664px; top: 240px; font-size: 56px; color: var(--ink); }
  .subhead { left: 664px; font-size: 32px; color: var(--ink); }
  .subhead.first { top: 289px; }
  .subhead.second { top: 337px; }

  .divider { position: absolute; left: 454px; top: 383px; width: 420px; height: 2px; background: var(--ink); }

  .service { left: 664px; font-size: 37px; color: var(--white); }

  .contact { font-size: 34px; color: var(--ink); }
  .contact.address { left: 468px; top: 953px; font-size: 36px; }
  .contact.web { left: 468px; top: 1000px; }
  .contact.email { left: 468px; top: 1047px; }
  .contact.phone { left: 468px; top: 1093px; }

  .footer-dark { position: absolute; left: 0; top: 1120px; width: 371px; height: 80px; background: var(--black); }
  .footer-teal { position: absolute; left: 371px; top: 1120px; width: 590px; height: 80px; background: var(--teal); }
  .license { position: absolute; right: 31px; top: 1152px; transform: translateY(-50%); font-size: 25px; color: var(--ink); white-space: nowrap; }
</style>
</head>
<body>
<div class="ad">
  <div class="side-column"></div>
  <div class="portrait" role="img" aria-label="Portrait photo of the therapist"></div>

  <div class="service-panel"></div>
  <div class="name-band">DANA ROWELL, MA, MFT</div>

  <div class="centered headline">Psychotherapy</div>
  <div class="centered subhead first">for Individuals,</div>
  <div class="centered subhead second">Couples and Families</div>
  <div class="divider"></div>

  <div class="centered service" style="top:429px">Parenting</div>
  <div class="centered service" style="top:489px">Depression</div>
  <div class="centered service" style="top:549px">Anxiety</div>
  <div class="centered service" style="top:609px">Life Transitions</div>
  <div class="centered service" style="top:669px">Divorce</div>
  <div class="centered service" style="top:729px">Couples Issues</div>
  <div class="centered service" style="top:789px">Women’s Issues</div>
  <div class="centered service" style="top:849px">Attachment and Neuroscience</div>

  <div class="centered contact address">418 Harbor Lane, Brookfield, CA 94999</div>
  <div class="centered contact web">www.danarowell.com</div>
  <div class="centered contact email">dana@danarowell.com</div>
  <div class="centered contact phone">555.014.2738</div>

  <div class="footer-dark"></div>
  <div class="footer-teal"></div>
  <div class="license">License# MFC48203</div>
</div>
</body>
</html>
```